Barrister at Law needs Business Card Design

Need a business card design for Barrister at Law. Double sided. Simple Neil Thorsby and Barrister at Law on one side with contact details on the other side. I would like a professional design using Black or Platinum. Details on reverse side would include qualifications - Bcom-Llb and Acc Spec Commercial Litigation. I have attached the logo. Contact details would include address/ Po Box/ Phone/Fax/Mobile/email. I would like to use raised print or spot gloss.

```html
<!DOCTYPE html>
<html lang="en">
<head>
<meta charset="utf-8">
<title>Neil Thorsby – Barrister at Law business card</title>
<link href="https://fonts.googleapis.com/css2?family=Open+Sans:wght@400;600&display=swap" rel="stylesheet">
<style>
  :root {
    --backdrop: #d9d6d1;
    --paper: #efeee9;
    --paper-edge: #d4d2cc;
    --brand-blue: #2ba3dc;
    --ink: #1b2430;
    --ink-soft: #2c3746;
    --white: #ffffff;
  }
  * { margin: 0; padding: 0; box-sizing: border-box; }
  html, body { width: 1200px; height: 918px; overflow: hidden; }
  body {
    background: var(--backdrop);
    font-family: "Open Sans", Arial, sans-serif;
    position: relative;
  }
  .card {
    position: absolute;
    left: 280px;
    width: 640px;
    height: 366px;
    background: var(--paper);
    border: 1px solid var(--paper-edge);
    box-shadow: 0 6px 18px rgba(0,0,0,0.12);
    overflow: hidden;
  }
  .card--front { top: 60px; }
  .card--back { top: 492px; }

  .front-mark {
    position: absolute;
    inset: 0;
    display: flex;
    flex-direction: column;
    align-items: center;
    justify-content: center;
    gap: 8px;
  }
  .front-mark__row {
    display: flex;
    align-items: center;
    gap: 14px;
  }
  .front-mark__square {
    width: 22px; height: 22px;
    background: var(--brand-blue);
  }
  .front-mark__name {
    font-size: 32px;
    font-weight: 600;
    color: var(--ink);
    letter-spacing: 0.5px;
    line-height: 1.2;
  }
  .front-mark__title {
    font-size: 17px;
    font-weight: 400;
    color: var(--ink-soft);
    letter-spacing: 2px;
    text-transform: uppercase;
    padding-left: 36px;
  }

  .back-art { position: absolute; inset: 0; }

  .holder {
    position: absolute;
    right: 30px;
    top: 34px;
    text-align: right;
    color: var(--white);
  }
  .holder__name { font-size: 30px; font-weight: 600; line-height: 1.1; }
  .holder__quals { font-size: 17px; font-weight: 400; line-height: 1.35; margin-top: 4px; }

  .contact {
    position: absolute;
    left: 318px;
    top: 186px;
    color: var(--ink-soft);
    font-size: 16px;
    line-height: 22.5px;
    list-style: none;
  }
  .contact li { display: flex; align-items: center; gap: 8px; }
  .contact__icon { width: 16px; height: 16px; flex: none; }
</style>
</head>
<body>

  <section class="card card--front" aria-label="Card front">
    <div class="front-mark">
      <div class="front-mark__row">
        <span class="front-mark__square"></span>
        <span class="front-mark__name">Neil Thorsby</span>
      </div>
      <span class="front-mark__title">Barrister at Law</span>
    </div>
  </section>

  <section class="card card--back" aria-label="Card back">
    <svg class="back-art" width="640" height="366" viewBox="0 0 640 366" aria-hidden="true">
      <rect width="640" height="366" fill="var(--brand-blue)"/>
      <path d="M0,160 C70,80 170,50 300,80 C420,110 500,180 640,170 L640,366 L0,366 Z" fill="var(--paper)"/>
      <path d="M30,118 C110,50 200,38 310,66 C430,96 510,168 640,160" fill="none" stroke="var(--white)" stroke-width="2.5"/>
      <circle cx="150" cy="262" r="70" fill="none" stroke="var(--ink)" stroke-width="3"/>
      <line x1="298" y1="180" x2="292" y2="346" stroke="var(--brand-blue)" stroke-width="1.5"/>
    </svg>

    <div class="holder">
      <div class="holder__name">Neil Thorsby</div>
      <div class="holder__quals">Bcom-Llb&amp;Acc.Spec.<br>(Comm Lit)</div>
    </div>

    <ul class="contact">
      <li>1260 Larkspur Court</li>
      <li>Juneau, Alaska 34821</li>
      <li>
        <svg class="contact__icon" viewBox="0 0 16 16" aria-label="Phone" role="img"><path d="M3 1.5l3 .5 1 3-2 1.3a9 9 0 0 0 4.7 4.7L11 9l3 1 .5 3-2 1.5C6.5 14 2 9.5 1.5 3.5z" fill="var(--brand-blue)"/></svg>
        614 205 7731
      </li>
      <li>
        <svg class="contact__icon" viewBox="0 0 16 16" aria-label="Mobile" role="img"><rect x="4" y="1" width="8" height="14" rx="1.5" fill="none" stroke="var(--brand-blue)" stroke-width="1.6"/><circle cx="8" cy="12.5" r="0.9" fill="var(--brand-blue)"/></svg>
        742 318 5096
      </li>
      <li>
        <svg class="contact__icon" viewBox="0 0 16 16" aria-label="Fax" role="img"><rect x="4" y="1" width="8" height="5" fill="var(--brand-blue)"/><rect x="1" y="6" width="14" height="6" rx="1" fill="var(--brand-blue)"/><rect x="4" y="10" width="8" height="5" fill="var(--white)" stroke="var(--brand-blue)" stroke-width="1.2"/></svg>
        529 760 4183
      </li>
      <li>
        <svg class="contact__icon" viewBox="0 0 16 16" aria-label="Email" role="img"><rect x="1" y="3" width="14" height="10" fill="var(--brand-blue)"/><path d="M1.5 3.5L8 9l6.5-5.5" fill="none" stroke="var(--white)" stroke-width="1.2"/></svg>
        mail@thorsbylaw.com
      </li>
      <li>
        <svg class="contact__icon" viewBox="0 0 16 16" aria-label="Website" role="img"><circle cx="8" cy="8" r="7" fill="var(--brand-blue)"/><ellipse cx="8" cy="8" rx="3" ry="7" fill="none" stroke="var(--white)" stroke-width="1"/><line x1="1" y1="8" x2="15" y2="8" stroke="var(--white)" stroke-width="1"/></svg>
        www.thorsbylaw.com
      </li>
    </ul>
  </section>

</body>
</html>
```